Online Shop Maren

We need a web design for an online shop, called "Lirvo Dune Jewels". The shop should have an extraordinary, elegant look, as shown in the Quellwick Advertising Picture in our Briefing.pdf (attached). Please have a look at our Briefing regarding website colours, background ideas, and elements to be included. The online shop is about professional jewellery design pieces, where each piece is handmade of high quality materials, also unique pieces and unique editions possible. It should attract extraordinary people and visualize that its a very individual and unique design jewellery. You can get an idea of whom it should attract by reading our target group. Colours to be used are jewellery-Velvet red, Black / anthracite, exclusive colours, silverish-white, bronze-brown and golden.

Please play around when designing with the image pictures we attach, preferably more vertical pictures, no panoramic pictures like in Brovenka Shop. Also include the BLACK logo of lirvo dune. We include the SITEMAP in the briefing and also another folder with product pictures you can use for the draft.

Regarding Functions, the store will have the SAME (technical) functions as this page:http://www.brovenka-shop.eu/ - using the "most famous" products/categories for the starting page, going into individual product pages by clicking these images and then leading to a detailed page for one product only.

Target Market(s)

Jewellery-lovers, who appreciate extraordinary things, creative economy/fashion-industries, stylists, Style consultants, outfitter, theatres, operas, production sites, Cocktail-, Dinner and Bridefashion, exclusive traditional costume stores, dancesports and tango argento dancers

Industry/Entity Type

Shop

Requirements
Must have
• Must include:
• Colours as per briefing
• Background ideas/images as per briefing/pictures sent
• Sitemap as per briefing
• Social buttons
• Logo
• Design for 3 pages: Starting page showing big images, attractive design and the 4 popular categories
• Subpage with different products of one category (i.e. bracelets)
• Detail page with one individual product only
Should not have
• no fresh, playful colours like yellow, orange, green, blue
• no cheap design, no panorama pictures

```html
<!DOCTYPE html>
<html lang="en">
<head>
<meta charset="utf-8">
<title>Lirvo Dune Jewels</title>
<link rel="stylesheet" href="https://fonts.googleapis.com/css2?family=Montserrat:wght@400;600;700&family=Open+Sans:ital,wght@0,400;0,600;1,600&display=swap">
<style>
:root{
  --bg:#232221;
  --bg-dark:#1b1a19;
  --topbar:#121212;
  --footer:#0b0b0b;
  --bottombar:#151515;
  --nav:#e2e2e2;
  --nav-text:#333;
  --accent:#9b2a1c;
  --white:#f2f2f2;
  --muted:#8d8d8d;
  --line:#3a3a3a;
  --card:#1a1a1a;
  --wine:#7a1a1a;
}
*{box-sizing:border-box;margin:0;padding:0}
html,body{width:1200px;height:1155px;overflow:hidden}
body{position:relative;background:linear-gradient(90deg,var(--bg-dark),var(--bg) 30%,#262524 60%,var(--bg-dark));font-family:"Open Sans",Arial,sans-serif;color:var(--white)}
.abs{position:absolute}
.topbar{left:0;top:0;width:1200px;height:33px;background:var(--topbar)}
.cart{left:150px;top:7px;display:flex;align-items:center;gap:8px;font-size:12px;font-style:italic;font-weight:600}
.cart small{font-style:normal;font-weight:400;color:#aaa;font-size:11px}
.social-top{left:909px;top:6px;display:flex;gap:2px}
.social-top span{width:17px;height:17px;background:#3b3b3b;border:1px solid #555}
.social-top span+span{background:#5a5a5a}
.account{left:961px;top:8px;font-size:12px;color:#ddd}
.account b{font-weight:400;margin:0 6px;color:#888}
.brand{left:0;width:1200px;top:48px;text-align:center}
.brand h1{font-weight:400;font-size:30px;letter-spacing:.5px}
.brand p{font-size:16px;margin-top:2px}
.nav{left:150px;top:124px;width:900px;height:37px;background:var(--nav);border-top:2px dashed #bbb}
.nav ul{list-style:none;display:flex;height:100%;align-items:center}
.nav li{font-size:12px;color:var(--nav-text);padding:0 14px}
.nav li.active{color:var(--accent);background:#f3f3f3;height:100%;line-height:35px}
.nav li.plain{background:#d6d6d6;height:100%;line-height:35px}
.caret{font-size:8px;margin-left:4px;color:#777}
.search{position:absolute;right:9px;top:7px;width:160px;height:22px;background:#111;color:#ccc;font-size:11px;padding:3px 8px}
.dropdown{left:150px;top:161px;width:115px;background:#f0f0f0;z-index:3;font-size:11px;color:#333}
.dropdown div{height:22px;line-height:22px;padding-left:15px}
.dropdown .on{background:#d4d4d4}
.hero{left:150px;top:161px;width:900px;height:408px;display:flex}
.hero div{height:100%}
.p1{width:280px;background:linear-gradient(160deg,#6b4a45,#a7a9a4 55%,#5b4c48)}
.p2{width:314px;background:linear-gradient(180deg,#7d6a4a,#b5303c 55%,#4f3a34)}
.p3{width:306px;background:linear-gradient(200deg,#b5aca4,#3b2f2c 50%,#d8d3cf)}
.arrow{top:346px;width:37px;height:37px;background:#2a2a2a;display:flex;align-items:center;justify-content:center}
.headline{left:150px;width:900px;top:392px;text-align:center;font-family:"Montserrat",sans-serif;font-weight:700;text-shadow:0 2px 4px rgba(0,0,0,.6)}
.headline h2{font-size:29px;letter-spacing:.3px}
.headline p{font-size:15px;margin-top:-3px}
.cta{left:539px;top:459px;width:113px;height:34px;background:#e8e8e8;color:var(--accent);font-family:"Montserrat",sans-serif;font-weight:700;font-size:13px;line-height:34px;text-align:center;box-shadow:0 2px 4px rgba(0,0,0,.5)}
.h3{font-family:"Montserrat",sans-serif;font-weight:600;font-size:14px;letter-spacing:.5px}
.newsletter-form{left:151px;top:626px;display:flex}
.newsletter-form .field{width:119px;height:18px;background:#f1f0e6;color:#222;font-size:9px;padding:3px 5px}
.newsletter-form .btn{width:55px;height:18px;background:#1a1a1a;border:1px solid #444;font-family:"Montserrat",sans-serif;font-size:10px;font-weight:600;line-height:16px;text-align:center;color:#ccc}
.divider{left:151px;top:663px;width:205px;height:1px;background:var(--line)}
.products{left:151px;top:700px;list-style:none;font-size:12px;color:var(--muted)}
.products li{height:24.7px}
.products .hover{color:#fff}
.card{width:220px;height:144px;border:1px solid #444;overflow:hidden}
.card .photo{position:absolute;inset:0}
.card .cap{position:absolute;left:0;right:0;bottom:0;height:44px;background:rgba(20,20,20,.78);padding:3px 6px}
.cap .name{font-size:13px;font-family:"Montserrat",sans-serif;color:#fff}
.cap .price{font-size:19px;color:#9a9a9a;line-height:20px}
.cap .add{position:absolute;right:6px;bottom:7px;width:47px;height:22px;border:1px solid #666;font-size:11px;color:#bbb;display:flex;align-items:center;justify-content:center;gap:3px;background:#222}
.cap .add.on{background:#8a8a8a;color:#eee}
.silver{background:radial-gradient(ellipse at 45% 45%,#d9d9d6,#6e6e6c 60%,#2c2c2c)}
.black{background:radial-gradient(ellipse at 50% 35%,#5a5a5a,#1c1c1c 55%,#2b2b2b)}
.bronze{background:radial-gradient(ellipse at 55% 45%,#b39a74,#5d5140 50%,#2a2723)}
.footer{left:0;top:977px;width:1200px;height:144px;background:var(--footer)}
.fcol{top:1003px;font-size:11px;color:var(--muted)}
.fcol h4{font-family:"Montserrat",sans-serif;font-weight:700;font-size:14px;color:#fff;margin-bottom:10px}
.fcol div{height:18px}
.fcol .on{color:#fff}
.sq{display:inline-block;width:8px;height:8px;background:var(--wine);margin-right:6px}
.news b{color:#ddd;font-weight:600;display:block;margin-bottom:4px}
.bottombar{left:0;top:1121px;width:1200px;height:34px;background:var(--bottombar);text-align:center;font-size:10px;color:#aaa;line-height:34px}
</style>
</head>
<body>
<div class="abs topbar"></div>
<div class="abs cart">
  <svg width="18" height="16" viewBox="0 0 18 16"><path d="M1 4h16l-2 10H3z" fill="none" stroke="#ddd" stroke-width="1.6"/><path d="M5 4l3-3M13 4l-3-3" stroke="#ddd" stroke-width="1.4"/></svg>
  <span>Shopping Cart <small>(00 items)</small></span>
</div>
<div class="abs social-top"><span></span><span></span></div>
<div class="abs account">Login<b>•</b>Check out</div>

<header class="abs brand">
  <h1>Lirvo Dune</h1>
  <p>♦ Jewels ♦</p>
</header>

<nav class="abs nav">
  <ul>
    <li class="active">Home<span class="caret">▼</span></li>
    <li class="plain">Online Shop<span class="caret">▼</span></li>
    <li>Info &amp; Facts<span class="caret">▼</span></li>
    <li>Partner<span class="caret">▼</span></li>
    <li>About me</li>
    <li>Contact</li>
  </ul>
  <div class="search">search
    <svg class="abs" style="right:5px;top:4px" width="13" height="13" viewBox="0 0 13 13"><circle cx="5.5" cy="5.5" r="4" fill="none" stroke="#fff" stroke-width="1.6"/><path d="M8.5 8.5l3.5 3.5" stroke="#fff" stroke-width="1.8"/></svg>
  </div>
</nav>

<section class="abs hero">
  <div class="p1" role="img" aria-label="Bride in white lace gown with pearl necklace, seen from behind"></div>
  <div class="p2" role="img" aria-label="Model in red dress wearing gold bracelet and earrings"></div>
  <div class="p3" role="img" aria-label="Model in white lace dress wearing pearl collier and bracelet"></div>
</section>
<div class="abs dropdown">
  <div>Collier</div><div>Bracelet</div><div class="on">Ring</div><div>Earring</div>
</div>
<div class="abs arrow" style="left:170px"><svg width="10" height="12" viewBox="0 0 10 12"><path d="M8 1L2 6l6 5z" fill="#bbb"/></svg></div>
<div class="abs arrow" style="left:987px"><svg width="10" height="12" viewBox="0 0 10 12"><path d="M2 1l6 5-6 5z" fill="#bbb"/></svg></div>
<div class="abs headline"><h2>NULLAM CURSUS MI UT LOREM</h2><p>COMMODO EU PHARETRA ELIT BLANDIT.</p></div>
<div class="abs cta">ONLINE SHOP</div>

<h3 class="abs h3" style="left:151px;top:599px">NEWSLETTER</h3>
<div class="abs newsletter-form"><div class="field">Enter your mail id</div><div class="btn">SUBMIT</div></div>
<div class="abs divider"></div>
<h3 class="abs h3" style="left:151px;top:676px">PRODUCTS</h3>
<ul class="abs products">
  <li>Collier</li><li>Ohrringe</li><li>Ring</li><li>Armbänder</li><li class="hover">Halsreif mit Perlen</li><li>Collier kristall</li><li>Collier gold</li><li>Armband</li><li>Halsband</li><li>Anhänger</li>
</ul>

<h3 class="abs h3" style="left:378px;top:599px">MOST POPULAR ITEMS</h3>

<div class="abs card" style="left:378px;top:644px"><div class="photo silver" role="img" aria-label="Crystal beaded bracelet"></div><div class="cap"><div class="name">sollicitudin lectus</div><div class="price">$ 000.00</div><div class="add on">add <svg width="14" height="12" viewBox="0 0 14 12"><path d="M0 1h3l2 7h7l1-5H4" fill="none" stroke="currentColor" stroke-width="1.4"/><circle cx="6" cy="10.5" r="1.2" fill="currentColor"/><circle cx="11" cy="10.5" r="1.2" fill="currentColor"/></svg></div></div></div>
<div class="abs card" style="left:603px;top:644px"><div class="photo black" role="img" aria-label="Black beaded collier on display stand"></div><div class="cap"><div class="name">sollicitudin lectus</div><div class="price">$ 000.00</div><div class="add">add <svg width="14" height="12" viewBox="0 0 14 12"><path d="M0 1h3l2 7h7l1-5H4" fill="none" stroke="currentColor" stroke-width="1.4"/><circle cx="6" cy="10.5" r="1.2" fill="currentColor"/><circle cx="11" cy="10.5" r="1.2" fill="currentColor"/></svg></div></div></div>
<div class="abs card" style="left:829px;top:644px"><div class="photo bronze" role="img" aria-label="Bronze beaded pendant"></div><div class="cap"><div class="name">sollicitudin lectus</div><div class="price">$ 000.00</div><div class="add">add <svg width="14" height="12" viewBox="0 0 14 12"><path d="M0 1h3l2 7h7l1-5H4" fill="none" stroke="currentColor" stroke-width="1.4"/><circle cx="6" cy="10.5" r="1.2" fill="currentColor"/><circle cx="11" cy="10.5" r="1.2" fill="currentColor"/></svg></div></div></div>
<div class="abs card" style="left:378px;top:803px"><div class="photo silver" role="img" aria-label="Silver lace collier on display stand"></div><div class="cap"><div class="name">sollicitudin lectus</div><div class="price">$ 000.00</div><div class="add">add <svg width="14" height="12" viewBox="0 0 14 12"><path d="M0 1h3l2 7h7l1-5H4" fill="none" stroke="currentColor" stroke-width="1.4"/><circle cx="6" cy="10.5" r="1.2" fill="currentColor"/><circle cx="11" cy="10.5" r="1.2" fill="currentColor"/></svg></div></div></div>
<div class="abs card" style="left:603px;top:803px"><div class="photo silver" role="img" aria-label="Crystal cluster ring"></div><div class="cap"><div class="name">sollicitudin lectus</div><div class="price">$ 000.00</div><div class="add">add <svg width="14" height="12" viewBox="0 0 14 12"><path d="M0 1h3l2 7h7l1-5H4" fill="none" stroke="currentColor" stroke-width="1.4"/><circle cx="6" cy="10.5" r="1.2" fill="currentColor"/><circle cx="11" cy="10.5" r="1.2" fill="currentColor"/></svg></div></div></div>
<div class="abs card" style="left:829px;top:803px"><div class="photo bronze" role="img" aria-label="Gold net collier on display stand"></div><div class="cap"><div class="name">sollicitudin lectus</div><div class="price">$ 000.00</div><div class="add">add <svg width="14" height="12" viewBox="0 0 14 12"><path d="M0 1h3l2 7h7l1-5H4" fill="none" stroke="currentColor" stroke-width="1.4"/><circle cx="6" cy="10.5" r="1.2" fill="currentColor"/><circle cx="11" cy="10.5" r="1.2" fill="currentColor"/></svg></div></div></div>

<footer class="abs footer"></footer>
<div class="abs fcol" style="left:151px"><h4>HOME</h4><div>Collier</div><div>Bracelet</div><div>Ring</div><div>Earring</div></div>
<div class="abs fcol" style="left:245px"><h4>SHOP</h4><div>Houte Coutur</div><div>Vouchers</div><div class="on">Collections</div></div>
<div class="abs fcol" style="left:348px"><h4>INFO</h4><div>Concept</div><div>Edition</div><div>Certificate</div></div>
<div class="abs fcol" style="left:440px"><h4>PARTNER</h4><div>Darvel</div><div>Tollmar</div><div>das Gewand</div></div>
<div class="abs fcol" style="left:553px"><h4>SOCIAL</h4><div><span class="sq"></span>Kinfold</div><div><span class="sq"></span>Chirpline</div><div><span class="sq"></span>Orbitplus</div><div><span class="sq"></span>Pinvale</div></div>
<div class="abs fcol news" style="left:663px;width:185px"><h4>LATEST NEWS</h4><b>Pretium a sodales</b><p>Nunc sapien lorem, pretium a sodales sit amet, dictum id tellus...read more</p><p style="margin-top:6px;color:#ccc">01.12.2013</p></div>
<div class="abs fcol" style="left:876px;width:180px"><h4>CONTACT US</h4><p>In vel turpis lacus, vitae fringilla urna. Etiam et tellus vel turpis cursus</p><p style="margin-top:12px"><b style="color:#fff">Tel:</b> 000-000-0000<br><b style="color:#fff">Email:</b> hello@lirvodune.com</p></div>
<div class="abs bottombar">© Copyright Lirvo Dune Jewels 2013. All Rights Resreved</div>
</body>
</html>
```